Business Card Design for Vintage Jazz

I am a vintage jazz band leader in New York City. My groups play the music of the 1920s, 1930s and 1940s. My website is morvalquist.com for more info on what I do.

I am looking for a two sided business card design that has the look and feel of a really nice business card from the 1930s. I need to convey with the design that my work has that vintage kind of class and style, but also conveys that we are fun and entertaining.

Most importantly it should make a bold staement. If Hal Denbrook had a card, what would it have looked like? I want a card that I feel confident will make an impact and will let people know that my work is te the top that NYC has to offer in vintage jazz..

Note that I have only decided to avoid the "committed payment" option as I have not used this service before. Assuming that I get quality work I will select a design from those presented.

Target Market(s)

people who want to hire my band for events, media, and new fans of the band

Industry/Entity Type

Performing Art

Contact Information for Business Card

Definitely a matte finish, possibly a sort of old style of paper with that brown tint? definitely a thick card.

Requirements
Must have
• FRONT
• My name: Tobin Vashley
• What I do: Bandleader, Guitarist, Vocalist, Songwriter
• Contact Details: morvalquist.com tobin@morvalquist.com 646-555-0148
• BACK
• My Social Media Links:
• facebook.morvalquist.com
• twitter, instagram, linkedin: morvalquist
• I'm also including a photo image I would like to use. The photo's background is not needed, and to be honest isn't really desireable. Just looking to use the image of me.
Nice to have
• I'm attaching which could be used as is, omitted from the card, or altered maybe with text going around the outside of the circle or in some other way. It may need some clean up to the edges of the lettering as we only use it for the website thumbnail.
• If there's space I'd like to include the text "join our mailing list for a free song download: freesong.morvalquist.com" If not perhaps just "Download a Free Song at: freesong.morvalquist.com - something to this end.
Should not have
• anything cartoony. Don't think retro 90s's vision of the swing era, think actual swing era!
• anything modern. Got to look old school
• Try to avoid dark backgrounds. Since we often play in bars and clubs where it is dar, a d
• avoid script fonts.

```html
<!DOCTYPE html>
<html lang="en">
<head>
<meta charset="utf-8">
<title>Tobin Vashley — Business Card</title>
<link rel="stylesheet" href="https://fonts.googleapis.com/css2?family=Open+Sans:wght@400;600;700&display=swap">
<style>
  :root {
    --canvas: #ececec;
    --paper: #ffffff;
    --teal: #5ec4b0;
    --teal-dark: #3fae99;
    --ink: #4a4a4a;
    --ink-dark: #1f1f1f;
    --white: #ffffff;
  }
  * { box-sizing: border-box; margin: 0; padding: 0; }
  html, body {
    width: 1200px; height: 795px; overflow: hidden;
    background: var(--canvas);
    font-family: "Open Sans", Arial, sans-serif;
  }
  .sheet {
    width: 1200px; height: 795px;
    display: flex; align-items: center; justify-content: center; gap: 40px;
  }
  .card {
    width: 540px; height: 309px; position: relative; overflow: hidden;
    box-shadow: 0 2px 10px rgba(0,0,0,0.12);
  }

  /* Front */
  .card--front {
    background: var(--paper);
    display: flex; flex-direction: column; align-items: center; justify-content: center;
    text-align: center; color: var(--ink);
  }
  .brand-mark {
    width: 62px; height: 62px; border-radius: 50%;
    background: var(--teal); margin-bottom: 10px;
  }
  .card--front .name {
    color: var(--teal); font-weight: 700; font-size: 30px; letter-spacing: 0.5px;
    line-height: 1.1; margin-bottom: 8px;
  }
  .card--front .roles {
    font-size: 12.5px; letter-spacing: 0.6px; word-spacing: 6px; margin-bottom: 4px;
  }
  .card--front .contact { font-size: 12.5px; margin-bottom: 2px; }
  .card--front .web { font-size: 12.5px; }
  .card--front .web .accent { color: var(--teal); }

  /* Back */
  .card--back { background: var(--teal); color: var(--white); }
  .portrait-ring {
    position: absolute; left: 84px; top: 56px; width: 210px; height: 210px;
    border-radius: 50%; border: 1px solid rgba(255,255,255,0.25);
  }
  .portrait {
    position: absolute; left: 70px; top: 30px; width: 220px; height: 279px;
    border-radius: 46% 46% 8px 8px / 30% 30% 8px 8px;
    background: linear-gradient(180deg, #d9d9d9 0%, #8a8a8a 35%, #2a2a2a 70%, #1a1a1a 100%);
  }
  .back-info {
    position: absolute; left: 300px; top: 112px; width: 230px;
  }
  .card--back .name { font-size: 31px; font-weight: 700; line-height: 1.1; white-space: nowrap; }
  .card--back .roles { font-size: 11.5px; margin-top: 4px; white-space: nowrap; }
  .social-row { display: flex; gap: 6px; margin-top: 12px; }
  .social-dot { width: 14px; height: 14px; border-radius: 50%; background: var(--ink-dark); }
  .card--back .web { font-size: 11.5px; letter-spacing: 3.2px; margin-top: 9px; white-space: nowrap; }
</style>
</head>
<body>
<main class="sheet">
  <section class="card card--front" aria-label="Card front">
    <div class="brand-mark" aria-hidden="true"></div>
    <h1 class="name">Tobin Vashley</h1>
    <p class="roles">BANDLEADER, GUITARIST, VOCALIST, SONGWRITER</p>
    <p class="contact">Phone: 646-555-0148, E-mail: tobin@morvalquist.com</p>
    <p class="web">www.<span class="accent">morvalquist</span>.com</p>
  </section>

  <section class="card card--back" aria-label="Card back">
    <div class="portrait-ring" aria-hidden="true"></div>
    <div class="portrait" role="img" aria-label="Black and white photo of the bandleader in a striped blazer tipping a straw boater hat"></div>
    <div class="back-info">
      <h2 class="name">Tobin Vashley</h2>
      <p class="roles">Bandleader, Guitarist, Vocalist, Songwriter</p>
      <div class="social-row" aria-label="Social media links">
        <span class="social-dot"></span><span class="social-dot"></span>
        <span class="social-dot"></span><span class="social-dot"></span>
        <span class="social-dot"></span><span class="social-dot"></span>
        <span class="social-dot"></span><span class="social-dot"></span>
      </div>
      <p class="web">www.morvalquist.com</p>
    </div>
  </section>
</main>
</body>
</html>
```